Hi,
We are also sourcing for a logo, if you have ideas please take a look at our other project (if you look at our profile you should be able to see it).
We are looking for a website that will be used to manage mobile devices. The feature set is rather small, users can Wipe, Lock, Locate devices as well as make them Ring or Speak (by sending text to be spoken). We attached some images of what it looks like right now. We are looking for simplicity, uniformity and most importantly, the website should be thought of as primary User Interface, it should flow.
Please see attached to get an idea of what it looks like now. The current design was inspired by making a site that will work and flow well on a variety of displays (from mobile to tablet to desktop).
We want to stay away from radio buttons, check-boxes. This should be engaging and creative, opposite of Corporate. Not busy (ideally we are looking to have fewest possible choices at any given time and at the same time no feature should be more than 3 clicks away (this is a suggestion/approximation... just want to share our understanding of what 'flow' is).
Could be cartoony.
Thanks!
BrisketLoom
Reason: there are a couple of designs that are interesting, in addition to specific feedback I provided, possibly looking for more concepts.
Thank You

```html
<!DOCTYPE html>
<html lang="en">
<head>
<meta charset="utf-8">
<title>BrisketLoom – Lost your phone?</title>
<link rel="stylesheet" href="https://fonts.googleapis.com/css2?family=Open+Sans:wght@300;400;600&family=Varela+Round&display=swap">
<style>
  :root {
    --topbar: #3db6ee;
    --hero-top: #2ea2e4;
    --hero-bottom: #1a7fc8;
    --nav-active: #5fcaf6;
    --white: #ffffff;
    --rule: rgba(255,255,255,0.45);
    --footer-text: #7a7a7a;
    --footer-rule: #d9d9d9;
    --badge: #2b2b2b;
    --badge-edge: #4a4a4a;
    --phone-dark: #3a3d42;
    --phone-light: #e9ecef;
  }
  * { margin: 0; padding: 0; box-sizing: border-box; }
  html, body { width: 1200px; height: 835px; overflow: hidden; background: var(--white); }
  body { font-family: "Open Sans", Arial, sans-serif; position: relative; }

  .topbar { position: absolute; left: 0; top: 0; width: 1200px; height: 48px; background: var(--topbar); }
  .social { position: absolute; top: 9px; width: 29px; height: 29px; border-radius: 50%; background: var(--white); }
  .social--one { left: 883px; }
  .social--two { left: 919px; }
  .search { position: absolute; left: 978px; top: 10px; width: 137px; height: 27px; background: var(--white);
            border: 1px solid #c9d6df; border-radius: 2px; font-size: 11px; font-style: italic; color: #a9b4bc;
            padding: 5px 9px; }
  .search svg { position: absolute; right: 7px; top: 7px; }

  .hero { position: absolute; left: 0; top: 48px; width: 1200px; height: 542px;
          background: radial-gradient(ellipse at 60% 20%, #3aaeea 0%, transparent 60%),
                      linear-gradient(to bottom, var(--hero-top), var(--hero-bottom)); }
  .below { position: absolute; left: 0; top: 590px; width: 1200px; height: 245px;
           background: linear-gradient(to bottom, #eef1f4, var(--white) 40%); }

  .brand { position: absolute; left: 86px; top: 68px; font-family: "Varela Round", Arial, sans-serif;
           font-size: 54px; color: var(--white); letter-spacing: -0.5px; }

  .nav { position: absolute; top: 93px; right: 84px; display: flex; }
  .nav a { display: block; height: 38px; line-height: 38px; padding: 0 23px; color: var(--white);
           font-size: 14px; text-decoration: none; text-transform: uppercase; }
  .nav a.is-active { background: var(--nav-active); }

  .rule { position: absolute; height: 1px; background: var(--rule); }
  .rule--header { left: 83px; top: 164px; width: 1033px; }
  .rule--h1 { left: 530px; top: 336px; width: 586px; }
  .rule--h2 { left: 530px; top: 427px; width: 586px; }

  .devices { position: absolute; left: 60px; top: 186px; width: 490px; height: 530px; }
  .phone { position: absolute; border-radius: 34px; }
  .phone--back { left: 36px; top: 70px; width: 154px; height: 386px;
                 background: linear-gradient(160deg, #5a5e64, var(--phone-dark)); }
  .phone--front { left: 185px; top: 2px; width: 254px; height: 498px;
                  background: linear-gradient(160deg, #ffffff, var(--phone-light)); border: 2px solid #6b6f74; }
  .phone-screen { position: absolute; left: 12px; top: 45px; right: 12px; bottom: 60px; border-radius: 2px; }
  .phone--back .phone-screen { background: linear-gradient(#8a9bab, #5e6a75); top: 50px; left: 10px; right: 10px; bottom: 46px; }
  .phone--front .phone-screen { background: linear-gradient(#e7e3d4, #cfd8c3); }
  .phone-shadow { position: absolute; left: 20px; top: 480px; width: 470px; height: 40px;
                  background: radial-gradient(ellipse, rgba(0,0,0,0.18), transparent 70%); }

  .headline { position: absolute; left: 527px; top: 240px; font-weight: 300; font-size: 62px;
              color: var(--white); letter-spacing: -0.5px; line-height: 1; }
  .features { position: absolute; left: 531px; top: 365px; width: 585px; display: flex;
              justify-content: space-between; list-style: none; }
  .features li { color: var(--white); font-size: 26px; display: flex; align-items: center; }
  .features li::before { content: ""; width: 12px; height: 12px; border-radius: 50%; background: var(--white);
                         margin-right: 17px; }
  .features li:nth-child(1) { width: 145px; }
  .features li:nth-child(2) { width: 160px; }
  .features li:nth-child(3) { width: 160px; }
  .intro { position: absolute; left: 531px; top: 455px; width: 585px; font-size: 12.5px; line-height: 23px;
           color: var(--white); text-align: justify; }

  .store-badge { position: absolute; left: 531px; top: 535px; width: 190px; height: 73px; border-radius: 8px;
                 background: linear-gradient(#3a3a3a, var(--badge)); border: 2px solid var(--badge-edge);
                 box-shadow: 0 3px 6px rgba(0,0,0,0.3); }

  .footer-rule { position: absolute; left: 83px; top: 742px; width: 1033px; height: 1px; background: var(--footer-rule); }
  .footer-nav { position: absolute; left: 84px; top: 772px; font-size: 13px; color: var(--footer-text); }
  .footer-nav span.sep { margin: 0 8px; }
  .copyright { position: absolute; right: 84px; top: 772px; font-size: 13px; color: var(--footer-text); }
  .copyright span { margin-left: 14px; }
</style>
</head>
<body>
  <header class="topbar">
    <span class="social social--one" aria-hidden="true"></span>
    <span class="social social--two" aria-hidden="true"></span>
    <div class="search">Search
      <svg width="11" height="11" viewBox="0 0 11 11"><circle cx="4.5" cy="4.5" r="3.3" fill="none" stroke="#b5bfc6" stroke-width="1.4"/><line x1="7" y1="7" x2="10" y2="10" stroke="#b5bfc6" stroke-width="1.6"/></svg>
    </div>
  </header>

  <section class="hero"></section>
  <div class="below"></div>

  <div class="brand">BrisketLoom</div>
  <nav class="nav">
    <a href="#" class="is-active">Home</a>
    <a href="#">About</a>
    <a href="#">Get the Application</a>
    <a href="#">Contact</a>
  </nav>
  <div class="rule rule--header"></div>

  <div class="devices">
    <div class="phone-shadow"></div>
    <div class="phone phone--back"><div class="phone-screen" role="img" aria-label="Smartphone showing a photo of a businesswoman on a call"></div></div>
    <div class="phone phone--front"><div class="phone-screen" role="img" aria-label="Smartphone showing a city map with a location pin and a speech bubble"></div></div>
  </div>

  <h1 class="headline">Lost your phone....?</h1>
  <div class="rule rule--h1"></div>
  <ul class="features">
    <li>Lock it</li>
    <li>Ring it</li>
    <li>Wipe it</li>
    <li>Find it</li>
  </ul>
  <div class="rule rule--h2"></div>
  <p class="intro">Sed ut perspiciatis unde omnis iste natus error sit voluptatem accusantium doloremque laudantium, totam rem aperiam, eaque ipsa quae ab illo inventore veritatis etquasi.</p>
  <a href="#" class="store-badge" aria-label="Download from the app store"></a>

  <div class="footer-rule"></div>
  <footer>
    <div class="footer-nav">Home<span class="sep">|</span>About<span class="sep">|</span>Get the Application<span class="sep">|</span>Contact<span class="sep">|</span>Privacy<span class="sep">|</span>Terms and Conditions</div>
    <div class="copyright">Copyright © 2012 www.brisketloom.com<span>All tights reserved.</span></div>
  </footer>
</body>
</html>
```